Maple Roster Business Card for recruitment company

We are looking for a Business Card Design that incorporates our personal details and our busines name and logo. We are a specialized search consultancy that recruit Property and Construction professionals.
We would like a business card that stands out and is appealing to the Construction and Property industry as well.

Target Market(s)

people in the construction and property industry

Contact Information for Business Card

Business Name and logo

Font styles to use
Serif

Colors
0094D4
00A9DD
6FCCEA
C7EBF8
E9F6FB

Requirements
Must have
• Business name and logo as well as contact details
Should not have
• No photos of us please

```html
<!DOCTYPE html>
<html lang="en">
<head>
<meta charset="utf-8">
<title>Maple Roster Business Card</title>
<link rel="stylesheet" href="https://fonts.googleapis.com/css2?family=Montserrat:wght@300;400;600&display=swap">
<style>
  :root {
    --bg: #6e6e6e;
    --bg-light: #8a8a8a;
    --teal: #023e52;
    --white: #ffffff;
    --ink-light: #e8f1f4;
  }
  * { margin: 0; padding: 0; box-sizing: border-box; }
  html, body { width: 1200px; height: 1015px; overflow: hidden; }
  body {
    background: radial-gradient(circle at 35% 45%, var(--bg-light), var(--bg) 75%);
    font-family: "Montserrat", sans-serif;
    position: relative;
  }
  .card {
    position: absolute;
    left: 250px;
    width: 700px;
    height: 400px;
    box-shadow: 0 10px 24px rgba(0,0,0,0.35);
    overflow: hidden;
  }
  .card--front { top: 80px; background: var(--teal); display: flex; align-items: center; justify-content: center; }
  .card--back { top: 535px; display: flex; }
  .brand {
    font-weight: 300;
    font-size: 46px;
    letter-spacing: 4px;
    text-transform: uppercase;
    white-space: nowrap;
  }
  .brand--light { color: var(--white); }
  .brand--dark { color: var(--teal); font-size: 40px; }
  .back__logo-side {
    width: 55%;
    background: var(--white);
    display: flex;
    align-items: center;
    justify-content: center;
  }
  .back__info-side {
    width: 45%;
    background: var(--teal);
    color: var(--white);
    padding: 70px 0 0 44px;
  }
  .person__name { font-weight: 600; font-size: 22px; letter-spacing: 0.5px; text-transform: uppercase; line-height: 1.1; }
  .person__role { font-weight: 400; font-size: 13px; letter-spacing: 0.8px; text-transform: uppercase; margin-bottom: 26px; color: var(--ink-light); }
  .contact { list-style: none; }
  .contact__item { display: flex; align-items: center; gap: 10px; font-size: 15px; line-height: 1.55; }
  .contact__icon { width: 15px; height: 15px; flex: none; }
  .address { font-size: 15px; line-height: 1.4; margin-top: 18px; padding-left: 25px; }
</style>
</head>
<body>
  <section class="card card--front">
    <span class="brand brand--light">Maple Roster</span>
  </section>

  <section class="card card--back">
    <div class="back__logo-side">
      <span class="brand brand--dark">Maple Roster</span>
    </div>
    <div class="back__info-side">
      <h1 class="person__name">Daniel Hart</h1>
      <p class="person__role">Managing Director</p>
      <ul class="contact">
        <li class="contact__item">
          <svg class="contact__icon" viewBox="0 0 16 16" fill="none" stroke="currentColor" stroke-width="1.6"><path d="M4 1.5l2.5 3-1.5 2a8 8 0 0 0 4.5 4.5l2-1.5 3 2.5-1.5 2.5C7 14.5 1.5 9 1.5 3.5z"/></svg>
          044-987 654 321
        </li>
        <li class="contact__item">
          <svg class="contact__icon" viewBox="0 0 16 16" fill="none" stroke="currentColor" stroke-width="1.5"><rect x="1" y="3" width="14" height="10"/><path d="M1 3l7 6 7-6"/></svg>
          hello@mapleroster.com
        </li>
        <li class="contact__item">
          <svg class="contact__icon" viewBox="0 0 16 16" fill="none" stroke="currentColor" stroke-width="1.3"><circle cx="8" cy="8" r="6.5"/><ellipse cx="8" cy="8" rx="3" ry="6.5"/><path d="M1.5 8h13M2.5 5h11M2.5 11h11"/></svg>
          www.mapleroster.com
        </li>
      </ul>
      <p class="address">421, Address line goes here<br>45452, Country Name</p>
    </div>
  </section>
</body>
</html>
```